Boutique town planning business needs a Business Card design

We need a business card design for a new company called The Zoning Bridgeway. We provide town planning and urban design services to government, business and community groups. We would like to see the designs use the colours in the logo (blue, deep red, green and amber), plenty of white and including black and grey in the writing. The final design should communicate collaboration, creativity and professionalism and that we are approachable.

Industry/Entity Type

Town

```html
<!DOCTYPE html>
<html lang="en">
<head>
<meta charset="utf-8">
<title>The Zoning Bridgeway – Business Card</title>
<link href="https://fonts.googleapis.com/css2?family=Exo+2:wght@400;500;600&family=Open+Sans:wght@600;700&display=swap" rel="stylesheet">
<style>
  :root {
    --page-bg: #e6e6e4;
    --card-white: #ffffff;
    --card-black: #0b0b0b;
    --accent-blue: #2596c9;
    --brand-green: #4c9a3a;
    --text-dark: #262626;
    --text-grey: #5a5a5a;
    --text-light: #f2f2f2;
  }
  html, body {
    margin: 0;
    width: 1200px;
    height: 899px;
    overflow: hidden;
    background: var(--page-bg);
  }
  .business-card {
    position: absolute;
    left: 100px;
    top: 164px;
    width: 1000px;
    height: 572px;
    border-radius: 44px;
    overflow: hidden;
    background: var(--card-white);
    box-shadow: 0 10px 30px rgba(0,0,0,0.18);
    font-family: "Exo 2", sans-serif;
  }
  .card-sweep {
    position: absolute;
    inset: 0;
  }
  .brand {
    position: absolute;
    left: 78px;
    top: 118px;
    display: flex;
    align-items: center;
    gap: 18px;
  }
  .brand-dot {
    width: 62px;
    height: 62px;
    border-radius: 50%;
    background: var(--brand-green);
  }
  .brand-name {
    font-family: "Open Sans", sans-serif;
    font-weight: 700;
    font-size: 38px;
    line-height: 1.05;
    color: var(--text-dark);
    letter-spacing: -0.5px;
  }
  .person {
    position: absolute;
    left: 82px;
    top: 318px;
  }
  .person-name {
    font-size: 30px;
    font-weight: 500;
    letter-spacing: 1.5px;
    color: var(--accent-blue);
    margin: 0;
  }
  .person-role {
    font-size: 19px;
    color: var(--text-grey);
    margin: 4px 0 0 6px;
  }
  .address {
    position: absolute;
    left: 88px;
    top: 420px;
    font-size: 23px;
    line-height: 1.45;
    color: var(--text-dark);
    letter-spacing: 0.5px;
  }
  .contact-list {
    position: absolute;
    right: 46px;
    top: 160px;
    margin: 0;
    padding: 0;
    list-style: none;
    color: var(--text-light);
    font-size: 19px;
    letter-spacing: 1px;
  }
  .contact-item {
    display: flex;
    justify-content: flex-end;
    align-items: center;
    gap: 12px;
    height: 40px;
  }
  .contact-icon {
    width: 20px;
    height: 20px;
    fill: var(--text-light);
  }
</style>
</head>
<body>
  <div class="business-card">
    <svg class="card-sweep" viewBox="0 0 1000 572" preserveAspectRatio="none" aria-hidden="true">
      <path d="M760 0 C720 250 570 470 330 572 L1000 572 L1000 0 Z" fill="var(--card-black)"/>
      <path d="M788 0 C760 130 712 245 640 330 C700 250 752 140 772 0 Z" fill="var(--accent-blue)"/>
    </svg>

    <div class="brand">
      <div class="brand-dot"></div>
      <div class="brand-name">The Zoning<br>Bridgeway</div>
    </div>

    <div class="person">
      <p class="person-name">MARTIN KELLER</p>
      <p class="person-role">Managing Director</p>
    </div>

    <div class="address">41 Ashgrove Lane, Level 3<br>Harbour Quarter</div>

    <ul class="contact-list">
      <li class="contact-item">021 555 0142
        <svg class="contact-icon" viewBox="0 0 24 24"><path d="M6.6 10.8a15 15 0 0 0 6.6 6.6l2.2-2.2a1 1 0 0 1 1-.25 11.4 11.4 0 0 0 3.6.6 1 1 0 0 1 1 1V20a1 1 0 0 1-1 1A17 17 0 0 1 3 4a1 1 0 0 1 1-1h3.5a1 1 0 0 1 1 1 11.4 11.4 0 0 0 .6 3.6 1 1 0 0 1-.25 1z"/></svg>
      </li>
      <li class="contact-item">082 555 0179
        <svg class="contact-icon" viewBox="0 0 24 24"><path d="M7 2h10a1 1 0 0 1 1 1v18a1 1 0 0 1-1 1H7a1 1 0 0 1-1-1V3a1 1 0 0 1 1-1zm1 3v13h8V5zm4 14.2a1 1 0 1 0 0 2 1 1 0 0 0 0-2z"/></svg>
      </li>
      <li class="contact-item">021 555 0143
        <svg class="contact-icon" viewBox="0 0 24 24"><path d="M7 2h8l3 3v5H7zM4 11h16a1 1 0 0 1 1 1v8a1 1 0 0 1-1 1H4a1 1 0 0 1-1-1v-8a1 1 0 0 1 1-1zm3 3v2h10v-2z"/></svg>
      </li>
      <li class="contact-item">hello@zoningbridge.com
        <svg class="contact-icon" viewBox="0 0 24 24"><path d="M3 5h18a1 1 0 0 1 1 1v12a1 1 0 0 1-1 1H3a1 1 0 0 1-1-1V6a1 1 0 0 1 1-1zm1 2.3V17h16V7.3l-8 5.2z M4.5 7l7.5 4.8L19.5 7z"/></svg>
      </li>
      <li class="contact-item">www.zoningbridge.com
        <svg class="contact-icon" viewBox="0 0 24 24"><path d="M12 2a10 10 0 1 0 0 20 10 10 0 0 0 0-20zm0 2c.9 1.2 1.6 2.6 2 4h-4c.4-1.4 1.1-2.8 2-4zM4.3 14a8 8 0 0 1 0-4h3.4a16 16 0 0 0 0 4zm.8 2h3c.3 1.3.8 2.5 1.4 3.6A8 8 0 0 1 5.1 16zm3-8h-3a8 8 0 0 1 4.4-3.6C8.9 5.5 8.4 6.7 8.1 8zM12 20c-.9-1.2-1.6-2.6-2-4h4c-.4 1.4-1.1 2.8-2 4zm2.3-6H9.7a14 14 0 0 1 0-4h4.6a14 14 0 0 1 0 4zm.2 5.6c.6-1.1 1.1-2.3 1.4-3.6h3a8 8 0 0 1-4.4 3.6zM16.3 14a16 16 0 0 0 0-4h3.4a8 8 0 0 1 0 4zm-.4-6c-.3-1.3-.8-2.5-1.4-3.6A8 8 0 0 1 18.9 8z"/></svg>
      </li>
    </ul>
  </div>
</body>
</html>
```